Calvanto Group Real Estate Company business cards

New business card design, we are generally happy with the basic layout of the existing front of business card, (feel free to change) but require a head shot photo on the back side.

http://www.calvanto.com.au/

Attached logos, and existing business card

------------------------------

Target Market(s)

Real estate

Industry/Entity Type

Real Estate

Contact Information for Business Card

Standard size double sided

Font styles to use
Other font styles liked:
• Futura

Requirements
Must have
• Photo head shot on the back side
Nice to have
• yes
Should not have
• No

```html
<!DOCTYPE html>
<html lang="en">
<head>
<meta charset="utf-8">
<title>Calvanto Group – Business Cards</title>
<link href="https://fonts.googleapis.com/css2?family=Jost:wght@400;500&family=Open+Sans:wght@400;600&display=swap" rel="stylesheet">
<style>
  :root{
    --bg:#3a3532;
    --card:#111112;
    --card-edge:#1b1b1d;
    --purple:#4a3a9c;
    --purple-light:#5d4db8;
    --orange:#f0a020;
    --white:#f2f2f2;
    --muted:#b9b9c0;
    --rule:#5a5a62;
    --photo-a:#2a3f73;
    --photo-b:#0e0e12;
  }
  *{box-sizing:border-box;margin:0;padding:0}
  html,body{width:1200px;height:814px;overflow:hidden}
  body{background:var(--bg);position:relative;font-family:"Open Sans",sans-serif}
  .card{
    position:absolute;width:540px;height:330px;background:var(--card);
    border:1px solid var(--card-edge);border-radius:4px;overflow:hidden;
    box-shadow:0 14px 30px rgba(0,0,0,.45);
  }
  .card--front{left:40px;top:242px}
  .card--back{left:620px;top:242px}

  /* front */
  .brand{position:absolute;left:46px;top:128px;text-align:center}
  .brand__name{font-family:"Jost",sans-serif;font-weight:400;font-size:50px;line-height:1;color:var(--purple);letter-spacing:.5px}
  .brand__tagline{margin-top:10px;font-size:12px;color:var(--purple);letter-spacing:1px;word-spacing:4px}
  .divider{position:absolute;left:292px;top:66px;width:1px;height:200px;background:linear-gradient(var(--card),var(--rule) 30%,var(--rule) 70%,var(--card))}
  .contact{position:absolute;left:312px;top:70px;color:var(--white);font-size:12.5px;line-height:19px}
  .contact__name{font-size:16px;font-weight:600;color:var(--purple-light);line-height:20px}
  .contact__role{font-size:13px;font-weight:600;color:var(--orange);margin-bottom:6px}
  .contact__row{display:flex;align-items:center;gap:8px}
  .contact__row svg{width:12px;height:12px;flex:none;fill:var(--purple-light)}
  .contact__spacer{width:12px;flex:none}

  /* back */
  .headshot{position:absolute;right:0;top:0;width:230px;height:220px;
    background:radial-gradient(ellipse at 55% 70%,var(--photo-a),var(--photo-b) 75%)}
  .brand--back{left:40px;top:200px;text-align:left}
  .brand--back .brand__name{color:var(--white);font-size:44px}
  .brand--back .brand__tagline{color:var(--muted);margin-top:6px;font-size:11px}
  .website{position:absolute;left:40px;top:282px;color:var(--white);font-size:13px;letter-spacing:3px}
</style>
</head>
<body>

<section class="card card--front">
  <div class="brand">
    <div class="brand__name">calvanto</div>
    <div class="brand__tagline">Buy | Sell | Rent</div>
  </div>
  <div class="divider"></div>
  <div class="contact">
    <div class="contact__name">Daniel Tran</div>
    <div class="contact__role">Director</div>
    <div class="contact__row"><span class="contact__spacer"></span>Calvanto Group</div>
    <div class="contact__row"><span class="contact__spacer"></span>ABN: 12 345 678 901</div>
    <div class="contact__row">
      <svg viewBox="0 0 24 24" aria-hidden="true"><path d="M6.6 10.8a15.2 15.2 0 0 0 6.6 6.6l2.2-2.2c.3-.3.7-.4 1-.2 1.1.4 2.3.6 3.6.6.6 0 1 .4 1 1V20c0 .6-.4 1-1 1A17 17 0 0 1 3 4c0-.6.4-1 1-1h3.5c.6 0 1 .4 1 1 0 1.3.2 2.5.6 3.6.1.3 0 .7-.2 1z"/></svg>
      0400 555 018
    </div>
    <div class="contact__row">
      <svg viewBox="0 0 24 24" aria-hidden="true"><path d="M2 5h20v14H2zm2 2v.4l8 5 8-5V7zm0 2.8V17h16V9.8l-8 5z"/></svg>
      daniel.tran@calvanto.com.au
    </div>
    <div class="contact__row">
      <svg viewBox="0 0 24 24" aria-hidden="true"><path d="M12 2a10 10 0 1 0 0 20 10 10 0 0 0 0-20zm6.9 9h-3a15 15 0 0 0-1.3-5.6A8 8 0 0 1 18.9 11zM12 4c.9 1.2 1.8 3.6 2 7h-4c.2-3.4 1.1-5.8 2-7zM9.4 5.4A15 15 0 0 0 8.1 11h-3a8 8 0 0 1 4.3-5.6zM5.1 13h3a15 15 0 0 0 1.3 5.6A8 8 0 0 1 5.1 13zM12 20c-.9-1.2-1.8-3.6-2-7h4c-.2 3.4-1.1 5.8-2 7zm2.6-1.4a15 15 0 0 0 1.3-5.6h3a8 8 0 0 1-4.3 5.6z"/></svg>
      www.calvanto.com.au
    </div>
  </div>
</section>

<section class="card card--back">
  <div class="headshot" role="img" aria-label="Head and shoulders photo of the director in a navy suit and blue tie"></div>
  <div class="brand brand--back">
    <div class="brand__name">calvanto</div>
    <div class="brand__tagline">Buy | Sell | Rent</div>
  </div>
  <div class="website">www.calvanto.com.au</div>
</section>

</body>
</html>
```